Modern Business Card

Modern professional business card with more than just logo and demographic info. Something memorable.

We are a trendy/modern chiropractic group with an emphasis on neurology, hence the minimalist-type brain logo. We want to convey that modern and technical aspect with professionalism and the elite nature of our practice environment.

```html
<!DOCTYPE html>
<html lang="en">
<head>
<meta charset="utf-8">
<title>Quillmere Chiropractic – Business Card</title>
<link rel="stylesheet" href="https://fonts.googleapis.com/css2?family=Libre+Baskerville&family=Montserrat:wght@400;500&display=swap">
<style>
  :root {
    --stage: #2b2b2d;
    --card: #1c1c1e;
    --card-back-a: #161617;
    --card-back-b: #2a2a2c;
    --white: #f4f4f4;
    --grey: #5e5e60;
    --blue: #3f7fd0;
    --serif: "Libre Baskerville", Georgia, serif;
    --sans: "Montserrat", Arial, sans-serif;
  }
  * { box-sizing: border-box; margin: 0; padding: 0; }
  html, body { width: 1200px; height: 900px; overflow: hidden; background: var(--stage); }
  .canvas { position: relative; width: 1200px; height: 900px; }
  .card {
    position: absolute; left: 250px; width: 700px; height: 400px;
    border-radius: 22px; overflow: hidden; background: var(--card);
    box-shadow: 0 14px 30px rgba(0,0,0,.45);
  }
  .card--back { top: 40px; }
  .card--front { top: 460px; }

  .back-pattern {
    position: absolute; inset: 0;
    background: linear-gradient(115deg, var(--card-back-a) 0%, var(--card-back-a) 40%, var(--card-back-b) 100%);
  }
  .back-brand {
    position: absolute; right: 45px; bottom: 75px;
    display: flex; align-items: center; gap: 12px;
    font-family: var(--serif); color: var(--white);
  }
  .back-brand__square { width: 30px; height: 30px; background: var(--white); }
  .back-brand__name { font-size: 20px; line-height: 1.05; letter-spacing: 1px; }
  .back-brand__name span { display: block; font-size: 11px; letter-spacing: 1.5px; }

  .wordmark { position: absolute; right: 50px; top: 62px; text-align: right; font-family: var(--serif); }
  .wordmark__name { font-size: 54px; line-height: 1; color: var(--white); letter-spacing: 2px; }
  .wordmark__sub { font-size: 31px; line-height: 1; color: var(--grey); letter-spacing: 1px; margin-top: -4px; }

  .divider { position: absolute; left: 45px; top: 190px; width: 520px; height: 1px; background: var(--blue); }

  .person { position: absolute; right: 50px; top: 204px; text-align: right; }
  .person__name { font-family: var(--serif); font-size: 28px; color: var(--white); letter-spacing: 1px; }
  .person__name .first { color: var(--blue); }
  .person__title { font-family: var(--sans); font-size: 17px; color: var(--white); margin-top: 4px; }

  .mark { position: absolute; left: 45px; top: 240px; font-family: var(--sans); font-weight: 500; font-size: 20px; color: var(--blue); }

  .address { position: absolute; left: 190px; top: 262px; font-family: var(--sans); font-style: normal; font-size: 18px; line-height: 1.35; color: var(--white); }

  .contact { position: absolute; right: 48px; top: 292px; list-style: none; font-family: var(--sans); font-size: 17px; color: var(--white); }
  .contact li { display: flex; justify-content: flex-end; align-items: center; gap: 10px; height: 27px; }
  .contact svg { width: 15px; height: 15px; fill: none; stroke: var(--blue); stroke-width: 1.6; }
</style>
</head>
<body>
<main class="canvas">
  <section class="card card--back">
    <div class="back-pattern" role="img" aria-label="Repeating tone-on-tone brand pattern"></div>
    <div class="back-brand">
      <div class="back-brand__square"></div>
      <div class="back-brand__name">QUILLMERE<span>CHIROPRACTIC</span></div>
    </div>
  </section>

  <section class="card card--front">
    <div class="wordmark">
      <div class="wordmark__name">QUILLMERE</div>
      <div class="wordmark__sub">CHIROPRACTIC</div>
    </div>
    <div class="divider"></div>
    <div class="person">
      <div class="person__name"><span class="first">MARK</span> ELLISON</div>
      <div class="person__title">Director</div>
    </div>
    <div class="mark">Quillmere</div>
    <address class="address">1187 Harlow Ridge<br>Salem, OR 97301</address>
    <ul class="contact">
      <li>(555) 214-0386
        <svg viewBox="0 0 16 16"><path d="M4 2l2.5 3-1.5 1.5c.8 1.8 2.2 3.2 4 4L10.5 9l3 2.5-1.5 2C7.5 13.5 2.5 8.5 2.5 4z"/></svg></li>
      <li>info@quillmerechiro.com
        <svg viewBox="0 0 16 16"><rect x="1.5" y="3.5" width="13" height="9" rx="1"/><path d="M1.5 4l6.5 5 6.5-5"/></svg></li>
      <li>www.quillmerechiro.com
        <svg viewBox="0 0 16 16"><circle cx="8" cy="8" r="6.5"/><ellipse cx="8" cy="8" rx="2.8" ry="6.5"/><path d="M1.5 8h13M2.5 5h11M2.5 11h11"/></svg></li>
    </ul>
  </section>
</main>
</body>
</html>
```